MRT Property - Business Cards

Looking for a business card & general letterhead, signage etc design for our new logo.

Colours:
000a20
0056a2
00b5ef
0088ce
68cef2

Fonts:
Poppins
Karla

Please keep look and feel of new brand - example in the zip package I sent.

```html
<!DOCTYPE html>
<html lang="en">
<head>
<meta charset="utf-8">
<title>MRT Property – Business Card</title>
<link rel="stylesheet" href="https://fonts.googleapis.com/css2?family=Poppins:wght@400;600;700&family=Karla:wght@400;500&display=swap">
<style>
  :root {
    --ink: #000a20;
    --brand-blue: #0056a2;
    --brand-cyan: #00b5ef;
    --brand-mid: #0088ce;
    --brand-light: #68cef2;
    --paper: #ffffff;
    --stage: #3d3d3d;
  }
  * { box-sizing: border-box; margin: 0; padding: 0; }
  html, body { width: 1200px; height: 803px; overflow: hidden; background: var(--stage); }
  .stage {
    position: relative; width: 1200px; height: 803px;
    display: flex; align-items: center; justify-content: center; gap: 60px;
  }
  .card {
    position: relative; width: 500px; height: 262px;
    border-radius: 18px; overflow: hidden;
    border: 1.5px solid var(--brand-light);
  }
  /* Front */
  .card--front { background: var(--paper); }
  .card__wave { position: absolute; inset: 0; width: 100%; height: 100%; }
  .holder { position: absolute; top: 20px; right: 30px; text-align: right; }
  .holder__name {
    font-family: "Poppins", sans-serif; font-weight: 700; font-size: 20px;
    color: var(--brand-blue); line-height: 1.1;
  }
  .holder__title {
    font-family: "Karla", sans-serif; font-size: 12px; color: var(--brand-cyan);
  }
  .brand {
    position: absolute; top: 76px; right: 62px;
    display: flex; align-items: center; gap: 10px;
  }
  .brand__dot { width: 14px; height: 14px; border-radius: 50%; background: var(--brand-cyan); }
  .brand__name {
    font-family: "Poppins", sans-serif; font-weight: 700; font-size: 28px;
    color: var(--brand-blue); letter-spacing: 0.3px;
  }
  .contact {
    position: absolute; left: 26px; bottom: 16px;
    font-family: "Karla", sans-serif; font-size: 11px; color: var(--paper);
    line-height: 1.4;
  }
  .contact__row { display: flex; align-items: center; gap: 6px; }
  .contact__row svg { width: 10px; height: 10px; flex: none; }
  .contact__address { margin-top: 4px; }
  /* Back */
  .card--back {
    background: linear-gradient(215deg, #1aa8ee 0%, var(--brand-mid) 30%, var(--brand-blue) 60%, #0a3f92 100%);
  }
  .card__pattern {
    position: absolute; inset: 0;
    background: radial-gradient(ellipse at 90% 15%, rgba(104,206,242,0.45) 0%, rgba(0,136,206,0) 55%),
                radial-gradient(ellipse at 5% 95%, rgba(0,10,32,0.35) 0%, rgba(0,10,32,0) 55%);
  }
  .back-brand {
    position: absolute; right: 36px; top: 150px;
    display: flex; align-items: center; gap: 7px;
    font-family: "Poppins", sans-serif; font-weight: 600; font-size: 14px; color: var(--paper);
  }
  .back-brand__dot { width: 9px; height: 9px; border-radius: 50%; background: var(--paper); }
</style>
</head>
<body>
<main class="stage">
  <section class="card card--front" aria-label="Business card front">
    <svg class="card__wave" viewBox="0 0 500 262" preserveAspectRatio="none" aria-hidden="true">
      <path d="M0 26 Q200 236 500 186 L500 262 L0 262 Z" fill="var(--brand-cyan)"/>
      <path d="M0 36 Q200 246 500 196 L500 262 L0 262 Z" fill="#ffffff"/>
      <path d="M0 40 Q200 250 500 200 L500 262 L0 262 Z" fill="var(--brand-blue)"/>
    </svg>
    <div class="holder">
      <p class="holder__name">Daniel Reyes</p>
      <p class="holder__title">President</p>
    </div>
    <div class="brand">
      <span class="brand__dot"></span>
      <span class="brand__name">MRT Property</span>
    </div>
    <div class="contact">
      <p class="contact__row">
        <svg viewBox="0 0 12 12"><path d="M3 1 L5 3.5 L4 5 Q5 7 7 8 L8.5 7 L11 9 L9.5 11 Q4 10.5 1 2.5 Z" fill="#fff"/></svg>
        555-210-4837</p>
      <p class="contact__row">
        <svg viewBox="0 0 12 12"><rect x="3" y="0.5" width="6" height="11" rx="1" fill="none" stroke="#fff"/><circle cx="6" cy="9.5" r="0.7" fill="#fff"/></svg>
        555-390-1626</p>
      <p class="contact__row">
        <svg viewBox="0 0 12 12"><rect x="0.5" y="2.5" width="11" height="7" fill="none" stroke="#fff"/><path d="M0.5 2.5 L6 7 L11.5 2.5" fill="none" stroke="#fff"/></svg>
        info@mrtproperty.com</p>
      <p class="contact__row">
        <svg viewBox="0 0 12 12"><circle cx="6" cy="6" r="5.2" fill="none" stroke="#fff"/><path d="M1 6 H11 M6 0.8 Q9 6 6 11.2 Q3 6 6 0.8" fill="none" stroke="#fff" stroke-width="0.8"/></svg>
        www.mrtproperty.com</p>
      <p class="contact__address">412 Harbor View Road<br>Seaford, Canada 20418</p>
    </div>
  </section>

  <section class="card card--back" aria-label="Business card back">
    <div class="card__pattern" role="img" aria-label="Repeating brand texture in blue and cyan tones"></div>
    <p class="back-brand"><span class="back-brand__dot"></span>MRT Property</p>
  </section>
</main>
</body>
</html>
```